Flyer for Compassion training days

I need a A5-size, single-sided flyer design for my training days. They are weekends in a blend of Compassionate Communication and Buddhist teachings called Gentlewise Dialogue. The logo for Gentlewise that should be included.
The flyer needs room for 1) course title, 2) course dates, location & price, 3) course description, 4) booking info, 5) my picture & short bio, and 6) the gentlewise.co website (yes, it is 'co' and not 'com).
Updates

Target Market(s)

Women 35-65 years, well-educated, spiritually minded. May have interests like yoga and meditation.

Industry/Entity Type

Health And Wellness

Font styles to use
Sans Serif
Other font styles liked:
• Blue Plaque, Josefina are both great

Colors
fbf289
fdf9cf
cfeae6
33b8a4

Requirements
Must have
• The Gentlewise logo; my picture.
• Elegance. Calm and expansive feel.
• The poster provided in the project files shows you the kind of information I need to include.
• Colours -- greens and yellows, but the options on craft plaza are not quite the right shades.
• The logo colour can be changed.
Nice to have
• Classy (but not cliche) image associated with Buddhism; gentle curves similar to those on the business card (see project files).
Should not have
• Dark background. Busy, loud design. Overly 'swirly' design. Images that I have to buy separately.

```html
<!DOCTYPE html>
<html lang="en">
<head>
<meta charset="utf-8">
<title>Gentlewise Dialogue – Core Course</title>
<link href="https://fonts.googleapis.com/css2?family=Baloo+2:wght@600;700&family=Arimo:ital,wght@0,400;0,700;1,400;1,700&display=swap" rel="stylesheet">
<style>
  :root {
    --green: #2f9e3b;
    --green-deep: #238a32;
    --green-light: #8cc84b;
    --green-pale: #cfe7a8;
    --cream: #fdf8dc;
    --cream-deep: #f8efc2;
    --ink: #2b2b2b;
    --white: #ffffff;
  }
  * { margin: 0; padding: 0; box-sizing: border-box; }
  html, body { width: 1200px; height: 848px; overflow: hidden; }
  body { background: var(--green); font-family: "Arimo", Arial, sans-serif; color: var(--ink); }

  .flyer { position: relative; width: 1200px; height: 848px; overflow: hidden; background: var(--green); }
  .backdrop { position: absolute; inset: 0; }

  .brand-badge {
    position: absolute; left: 20px; top: 20px; width: 147px; height: 147px;
    background: var(--white); border-radius: 10px 10px 44px 10px;
    display: flex; align-items: center; justify-content: center;
    font-family: "Baloo 2", sans-serif; font-weight: 700; font-size: 25px; color: var(--green);
  }

  .equation {
    position: absolute; left: 177px; top: 40px; white-space: nowrap;
    font-family: "Baloo 2", sans-serif; font-weight: 700; font-size: 38px; color: var(--white);
  }

  .leaf-glow {
    position: absolute; left: 520px; top: 180px; width: 420px; height: 520px;
    background: radial-gradient(ellipse at center, rgba(200,214,140,0.45), rgba(200,214,140,0) 70%);
  }

  .course-name {
    position: absolute; left: 0; width: 1306px; top: 136px; text-align: center;
    font-family: "Baloo 2", sans-serif; font-weight: 700; font-size: 48px; color: var(--green-deep);
  }

  .core-heading {
    position: absolute; left: 207px; top: 226px;
    font-weight: 700; font-style: italic; font-size: 40px; color: var(--green);
  }

  .intro {
    position: absolute; left: 104px; top: 318px; width: 512px;
    font-size: 21px; line-height: 28px; text-align: justify;
  }

  .explore {
    position: absolute; left: 104px; top: 474px; width: 512px;
    font-size: 21px; line-height: 28px;
  }
  .explore h3 { font-size: 21px; font-weight: 700; color: var(--green); }
  .explore ul { list-style: none; }
  .explore li { padding-left: 14px; text-indent: -14px; }
  .explore li::before { content: "* "; }

  .event-meta {
    position: absolute; left: 660px; width: 520px; top: 228px; text-align: center;
    font-size: 27px; line-height: 33px;
  }

  .audience {
    position: absolute; left: 664px; top: 318px; width: 507px;
    font-size: 21px; line-height: 28px; text-align: justify;
  }

  .booking {
    position: absolute; left: 664px; top: 514px; width: 507px;
    font-size: 21px; line-height: 28px; font-weight: 700; color: var(--green); text-align: justify;
  }

  .stones {
    position: absolute; left: 0; top: 660px; width: 205px; height: 188px;
    background: radial-gradient(ellipse at 40% 65%, #6b6b66 0%, #8e8f86 35%, #7fbf4a 65%, rgba(127,191,74,0) 90%);
  }

  .portrait {
    position: absolute; left: 213px; top: 667px; width: 112px; height: 141px;
    border-radius: 6px; background: linear-gradient(160deg, #d9d9d9, #8d8d8d);
    box-shadow: 0 0 0 3px rgba(255,255,255,0.6);
  }

  .bio {
    position: absolute; left: 341px; top: 666px; width: 823px;
    font-size: 21px; line-height: 28px;
  }
  .bio .credit { text-align: justify; margin-bottom: 10px; }
  .bio .label { font-weight: 700; }
  .bio .about { font-style: italic; }
  .bio .offer { font-weight: 700; }

  .site-badge {
    position: absolute; left: 924px; top: 757px; width: 262px; height: 84px;
    background: var(--white); border-radius: 10px 10px 30px 10px;
    display: flex; align-items: center; justify-content: center; gap: 12px;
    font-family: "Arimo", sans-serif; font-size: 26px; color: var(--green);
  }
  .site-badge .dot { width: 18px; height: 18px; border-radius: 50%; background: var(--green); }
</style>
</head>
<body>
<main class="flyer">
  <svg class="backdrop" width="1200" height="848" viewBox="0 0 1200 848" aria-hidden="true">
    <defs>
      <linearGradient id="creamFill" x1="0" y1="0" x2="1" y2="1">
        <stop offset="0" stop-color="#fefbe6"/>
        <stop offset="1" stop-color="#f8efc2"/>
      </linearGradient>
    </defs>
    <path d="M40 130 C 220 90, 500 70, 760 95 C 930 112, 1080 100, 1200 90 L 1200 200 C 1050 150, 820 130, 560 130 C 330 130, 150 170, 40 230 Z" fill="#5fb344" opacity="0.7"/>
    <path d="M600 108 C 800 90, 1020 100, 1200 130" stroke="var(--green-light)" stroke-width="10" fill="none" opacity="0.8"/>
    <path d="M205 118 C 520 100, 900 112, 1200 138 L 1200 808 C 900 830, 520 822, 190 812 C 110 785, 76 710, 76 580 L 76 340 C 76 225, 115 150, 205 118 Z" fill="url(#creamFill)"/>
    <path d="M20 440 C 30 330, 70 230, 150 170" stroke="var(--green-light)" stroke-width="7" fill="none" opacity="0.75"/>
    <path d="M1200 152 C 1060 125, 900 118, 760 128" stroke="var(--green-pale)" stroke-width="5" fill="none"/>
  </svg>

  <div class="leaf-glow" role="img" aria-label="Faint green leaf motif behind the text"></div>

  <div class="brand-badge">Gentlewise</div>
  <h1 class="equation">Mindfulness + Kindness + Compassionate Communication =</h1>
  <h2 class="course-name">Gentlewise Dialogue</h2>

  <h3 class="core-heading">Core Course:</h3>
  <p class="intro">Gentlewise Dialogue can help you increase awareness &amp; compassion in everyday speech (with yourself &amp; others), better understand your own patterns, and build resilience to challenging situations. Choose from:</p>

  <section class="explore">
    <h3>In this 2-day Core Course, we’ll explore:</h3>
    <ul>
      <li>Compassionate Communication;</li>
      <li>Buddhist teachings on Right Speech, loving kindness, Right Effort, and more;</li>
      <li>mindfulness practices;</li>
      <li>choices available to us in our everyday speech.</li>
    </ul>
  </section>

  <p class="event-meta">11-12 Dec • Larchfield Centre, Edinburgh<br>(£125/100)</p>

  <p class="audience">This workshop will be of interest if you’d like to improve personal and/or professional relationships. Open to all, best suited to those with at least 1 year’s experience with Mindfulness, Buddhism, or Compassionate Communication / NVC.</p>

  <p class="booking">Booking: Book online at Ovelbrook or write maren@gentlewise.co</p>

  <div class="stones" role="img" aria-label="Stacked grey pebbles with fresh green leaves"></div>
  <div class="portrait" role="img" aria-label="Portrait photo of the facilitator"></div>

  <section class="bio">
    <p class="credit"><span class="label">Facilitator:</span> <span class="about">Maren Holloway is an experienced group facilitator, having worked with a range of organisations and presented at a number of festivals &amp; conferences.</span></p>
    <p class="offer">Maren offers coaching in Gentlewise Dialogue.</p>
  </section>

  <div class="site-badge"><span class="dot"></span>gentlewise.co</div>
</main>
</body>
</html>
```